Moderne Visitenkarten für Medizintechnikfirma
Zielgruppe
Vertriebsfirma von moderner und innovativer Medizintechnik
Zielgruppe: Ärzte, Kliniken, Medizintechnikfirmen, Patienten
Aufgabenstellung
Besonderes, modernes, auffälliges und ansprechendes Design ohne überladen oder aufdringlich zu sein
Farbenorientierung kann am Logo und der Website geschehen. Wenn zum Logo harmonierend, sind aber auch andere Farben gerne gesehen.
Format: eher horizontal, vertikal aber auch möglich, abgerundete Ecken einplanen
Wenn möglich folgende Infos bitte schon auf die Karten bringen (pro Person eine Karte):
Konrad Faltermann (CEO)
konrad.faltermann@vitalis-partner.de
(Vitalis Partner GmbH
Lindenhof 12
26210 Grünstedt)
www.vitalis-partner.de
info@vitalis-partner.de
Jonas Prasken (CoS)
jonas.prasken@vitalis-partner.de
Die allgemeinen Firmeninfos können deutlich kleiner sein. Anschrift nur wenn es dadurch nicht zu viel werden würde.

```html
<!DOCTYPE html>
<html lang="de">
<head>
<meta charset="utf-8">
<title>Vitalis Partner – Visitenkarten</title>
<link href="https://fonts.googleapis.com/css2?family=Lato:wght@400;700&display=swap" rel="stylesheet">
<style>
  :root {
    --page: #eceef1;
    --card-light: #dfe0e6;
    --card-light-2: #ebecf0;
    --violet: #3b3366;
    --violet-deep: #2c2754;
    --violet-soft: #4a4180;
    --accent: #e0502a;
    --white: #ffffff;
  }
  * { box-sizing: border-box; margin: 0; padding: 0; }
  html, body { width: 1200px; height: 720px; overflow: hidden; }
  body {
    background: var(--page);
    font-family: "Lato", Arial, sans-serif;
    position: relative;
  }
  .card {
    position: absolute;
    top: 195px;
    width: 540px;
    height: 330px;
    border-radius: 18px;
    overflow: hidden;
    box-shadow: 0 6px 18px rgba(40, 36, 80, 0.12);
  }
  .card-front { left: 40px; }
  .card-back { left: 620px; }
  .card-texture {
    position: absolute; inset: 0;
  }
  .card-front .card-texture {
    background: radial-gradient(circle at 20% 70%, var(--card-light-2), var(--card-light) 70%);
  }
  .card-back .card-texture {
    background: radial-gradient(circle at 25% 80%, var(--violet-soft), var(--violet) 55%, var(--violet-deep));
  }
  .brand {
    position: absolute;
    display: flex;
    align-items: center;
    gap: 12px;
    font-weight: 700;
    letter-spacing: 0.2px;
  }
  .brand-dot { width: 22px; height: 22px; border-radius: 50%; }
  .card-front .brand { left: 70px; top: 62px; font-size: 34px; color: var(--violet); }
  .card-front .brand-dot { background: var(--accent); }
  .card-back .brand { left: 70px; top: 140px; font-size: 30px; color: var(--white); }
  .card-back .brand-dot { background: var(--white); }
  .rule { position: absolute; height: 2px; background: var(--violet); }
  .rule-top { left: 70px; right: 30px; top: 124px; }
  .rule-name { left: 0; width: 290px; top: 282px; }
  .contact-list {
    position: absolute; left: 270px; top: 150px;
    list-style: none; color: var(--violet);
    font-size: 15px;
  }
  .contact-list li { display: flex; align-items: center; gap: 10px; margin-bottom: 10px; }
  .contact-list svg { width: 18px; height: 18px; flex: none; }
  .person { position: absolute; left: 30px; top: 222px; }
  .person-name { font-size: 24px; font-weight: 700; color: var(--violet); }
  .person-role { font-size: 17px; color: var(--accent); margin-top: 4px; }
  .company-info {
    position: absolute; right: 30px; bottom: 34px;
    text-align: right; color: var(--white);
    font-size: 15px; line-height: 1.35;
  }
  .company-name { font-weight: 700; margin-bottom: 8px; }
</style>
</head>
<body>

<section class="card card-front">
  <div class="card-texture" role="img" aria-label="Helles Grau mit feinem Netzwerk aus Linien und Punkten"></div>
  <div class="brand"><span class="brand-dot"></span>Vitalis Partner</div>
  <div class="rule rule-top"></div>
  <ul class="contact-list">
    <li>
      <svg viewBox="0 0 24 24" fill="none" stroke="var(--accent)" stroke-width="2" stroke-linecap="round" stroke-linejoin="round"><path d="M5 3h4l2 5-2.5 1.5a11 11 0 0 0 6 6L16 13l5 2v4a2 2 0 0 1-2 2A17 17 0 0 1 3 5a2 2 0 0 1 2-2z"/></svg>
      <span>+4917640295837</span>
    </li>
    <li>
      <svg viewBox="0 0 24 24" fill="none" stroke="var(--accent)" stroke-width="2" stroke-linejoin="round"><rect x="3" y="5" width="18" height="14" rx="1"/><path d="M3 6l9 7 9-7"/></svg>
      <span>konrad.faltermann@vitalis-partner.de</span>
    </li>
  </ul>
  <div class="person">
    <p class="person-name">Konrad Faltermann</p>
    <p class="person-role">CEO</p>
  </div>
  <div class="rule rule-name"></div>
</section>

<section class="card card-back">
  <div class="card-texture" role="img" aria-label="Dunkles Violett mit feinem Netzwerk aus Linien und Punkten"></div>
  <div class="brand"><span class="brand-dot"></span>Vitalis Partner</div>
  <address class="company-info" style="font-style: normal;">
    <p class="company-name">Vitalis Partner GmbH</p>
    <p>Lindenhof 12, 26210 Grünstedt</p>
    <p>www.vitalis-partner.de</p>
    <p>info@vitalis-partner.de</p>
    <p>0800-5518320</p>
  </address>
</section>

</body>
</html>
```